Velan Tea Label & packaging for a premium tea brand. For local and global market

Create a look and feel for a box and rectangle tin. We are looking for a luxe packaging design for a new tea brand based in Kenya called 'Velan Tea'. Kenya is home to the finest teas in the world and Velan tea looks to embody that fact. Velan Tea uses the most premium of Kenyan Tea, Black tea, Purple tea, White Tea, Green tea, Hibiscus Tea and Moringa Tea. Velan Tea is handpicked from Kenya's highlands. This project will include the look and feel of the different teas described above. The copy on the main face of the box should read 'Premium Kenyan Tea' The box will contain 25 tagged tea bags, with a net weight of 50 gms.

On one side of the box will read 'packaging instructions' To fully savour this Velan premium tea, use one tea bag for each cup, add some freshly bolded water and wait for 2 minutes as you enjoy the sweet aroma of our tea, stir and serve' Ingredients : Black Tea, and for the others the same : Hibiscus Tea, Green Tea, Purple Tea, White tea. should also feature on the label: Produce of Kenya.

Target Market(s)

Premium

Industry/Entity Type

Agribusiness

Font styles to use
Script

Colors

Designer to choose colors to be used in the design.

Requirements
Must have
• Luxe look and feel
Nice to have
• I have attached the Velan tea logo and images of brands I'd lile the designer to be inspired by.
Should not have
• Green and yellow colours

```html
<!DOCTYPE html>
<html lang="en">
<head>
<meta charset="utf-8">
<title>Velan Tea – Side Label</title>
<link href="https://fonts.googleapis.com/css2?family=Gelasio:ital,wght@0,700;1,400&family=Bebas+Neue&display=swap" rel="stylesheet">
<style>
  :root {
    --backdrop: #c4c9d1;
    --tin-black: #232122;
    --label-white: #ffffff;
    --frame-line: #d9d9d9;
    --flag-red: #b8202a;
    --flag-green: #1f7a3a;
    --flag-black: #111111;
  }
  html, body {
    margin: 0;
    padding: 0;
    width: 1200px;
    height: 913px;
    overflow: hidden;
    background: var(--backdrop);
  }
  .canvas {
    position: relative;
    width: 1200px;
    height: 913px;
  }
  .side-panel {
    position: absolute;
    left: 380px;
    top: 230px;
    width: 452px;
    height: 486px;
    background: var(--tin-black);
    border-radius: 6px;
  }
  .label-frame {
    position: absolute;
    left: 62px;
    top: 125px;
    width: 338px;
    height: 289px;
    border: 1px solid var(--frame-line);
  }
  .label-heading {
    position: absolute;
    left: 50%;
    top: -26px;
    transform: translateX(-50%);
    margin: 0;
    padding: 0 8px;
    background: var(--tin-black);
    color: var(--label-white);
    font-family: "Gelasio", Georgia, serif;
    font-weight: 700;
    font-size: 19px;
    line-height: 21px;
    letter-spacing: 1.4px;
    text-align: center;
    white-space: nowrap;
  }
  .brewing-copy {
    position: absolute;
    left: 0;
    right: 0;
    top: 40px;
    margin: 0;
    color: var(--label-white);
    font-family: "Gelasio", Georgia, serif;
    font-style: italic;
    font-size: 20.5px;
    line-height: 24px;
    letter-spacing: 1.2px;
    text-align: center;
  }
  .origin-line {
    position: absolute;
    left: 0;
    right: 0;
    top: 247px;
    display: flex;
    justify-content: center;
    align-items: center;
    gap: 10px;
    color: var(--label-white);
    font-family: "Bebas Neue", Impact, sans-serif;
    font-size: 21px;
    letter-spacing: 0.8px;
    line-height: 1;
  }
  .flag-icon {
    width: 24px;
    height: 21px;
    display: block;
  }
</style>
</head>
<body>
<div class="canvas">
  <section class="side-panel">
    <div class="label-frame">
      <h2 class="label-heading">PACKAGING<br>INSTRUCTIONS</h2>
      <p class="brewing-copy">
        To fully savour this Velan<br>
        premium tea, use one tea<br>
        bag for each cup, add<br>
        some freshly bolded water<br>
        and wait for 2 minutes as<br>
        you enjoy the sweet aroma<br>
        of our tea, stir and serve'<br>
        Ingredients
      </p>
      <div class="origin-line">
        <svg class="flag-icon" viewBox="0 0 24 21" aria-hidden="true">
          <rect x="0" y="0" width="24" height="21" rx="2" fill="var(--label-white)"/>
          <rect x="0" y="0" width="24" height="6" rx="2" fill="var(--flag-black)"/>
          <rect x="0" y="7.5" width="24" height="6" fill="var(--flag-red)"/>
          <rect x="0" y="15" width="24" height="6" rx="2" fill="var(--flag-green)"/>
        </svg>
        <span>PRODUCT OF KENYA</span>
      </div>
    </div>
  </section>
</div>
</body>
</html>
```